MBR - Stationery Design Project

We need stationery based on our logo.

Company info :
Cabinet Voisard & Associés
Société à responsabilité limitée au capital de 200.000 FCFP
RCS Papeete 27586K - Numéro tahiti K73962
Centre d’affaires OPALE - Rue Gaston Perrin
BP 61384 MAHU POTE - 98752 Papeete
Tahiti - Polynésie française
Tél : +689 40 73 16 48
Fax : +689 40 39 64 91

Industry/Entity Type

It Company

Font styles to use
Sans Serif

```html
<!DOCTYPE html>
<html lang="fr">
<head>
<meta charset="utf-8">
<title>Cabinet Voisard &amp; Associés – Cartes de visite</title>
<link rel="stylesheet" href="https://fonts.googleapis.com/css2?family=Josefin+Sans:ital,wght@0,300;0,400;1,300&display=swap">
<style>
  :root {
    --backdrop: #e6e6e6;
    --paper: #ffffff;
    --navy: #1b3258;
    --slate: #8c9a9b;
    --ink: #4a4f55;
  }
  html, body {
    margin: 0;
    width: 1200px;
    height: 1000px;
    overflow: hidden;
    background: var(--backdrop);
    font-family: "Josefin Sans", sans-serif;
  }
  .card {
    position: absolute;
    width: 500px;
    height: 290px;
    background: var(--paper);
    box-shadow: 0 2px 6px rgba(0,0,0,0.12);
    overflow: hidden;
  }
  .card svg.bands { position: absolute; inset: 0; }
  .card--front { left: 90px; top: 170px; }
  .card--back { left: 610px; top: 540px; }

  .brand {
    position: absolute;
    display: flex;
    align-items: flex-start;
    gap: 10px;
    color: var(--navy);
    font-weight: 400;
  }
  .brand__mark {
    flex: none;
    background: var(--navy);
  }
  .brand__name { margin: 0; line-height: 1.15; }

  .card--front .brand { left: 262px; top: 108px; }
  .card--front .brand__mark { width: 14px; height: 14px; margin-top: 4px; }
  .card--front .brand__name { font-size: 22px; width: 180px; }

  .card--back .brand { right: 36px; top: 34px; }
  .card--back .brand__mark { width: 10px; height: 10px; margin-top: 2px; }
  .card--back .brand__name { font-size: 14px; }

  .contact { position: absolute; left: 32px; top: 142px; color: var(--ink); }
  .contact__name { font-size: 25px; font-weight: 300; margin: 0; }
  .contact__role { font-size: 15px; font-weight: 300; font-style: italic; margin: 4px 0 8px; }
  .contact__line { font-size: 9.5px; font-weight: 300; margin: 0 0 3px; }
</style>
</head>
<body>

<section class="card card--front" aria-label="Recto">
  <svg class="bands" width="500" height="290" viewBox="0 0 500 290" aria-hidden="true">
    <polygon points="0,145 250,145 238,215 0,215" fill="var(--navy)"/>
    <polygon points="418,40 462,40 476,100 404,100" fill="var(--slate)"/>
  </svg>
  <div class="brand">
    <span class="brand__mark" aria-hidden="true"></span>
    <p class="brand__name">Cabinet Voisard &amp; Associés</p>
  </div>
</section>

<section class="card card--back" aria-label="Verso">
  <svg class="bands" width="500" height="290" viewBox="0 0 500 290" aria-hidden="true">
    <polygon points="0,266 382,252 382,290 0,290" fill="var(--navy)"/>
    <polygon points="392,240 500,236 500,258 392,262" fill="var(--slate)"/>
  </svg>
  <div class="brand">
    <span class="brand__mark" aria-hidden="true"></span>
    <p class="brand__name">Cabinet Voisard &amp; Associés</p>
  </div>
  <div class="contact">
    <p class="contact__name">Marc Tehani</p>
    <p class="contact__role">Managing Director</p>
    <p class="contact__line">Centre d’affaires OPALE - Rue Gaston Perrin BP 61384 MAHU POTE -</p>
    <p class="contact__line">98752 Papeete, Tahiti - Polynésie française</p>
    <p class="contact__line">Tél : +689 40 73 16 48 | Fax : +689 40 39 64 91</p>
  </div>
</section>

</body>
</html>
```